Wordpress website for a new Podcast

Hi, We are looking for a designer to create a wordpress website project for a new podcast and publish it on the domain we own.

The show is called “Bright Gatherings” (logo included) and its aim is to interview guests who work as professional facilitators, trainers, teachers and coaches. The show has a positive vibe, is fun, vibrant and full of positive energy. These are the feelings we want to convey in the design.

The website should have a similar structure to: https://www.plumvesselcast.example/ with the following content:

1) The main page including:
- navigation bar and social buttons at the top
- main graphic design featuring the latest episode
- "latest episodes" section displaying 3 episodes (please design a mask to be used for new episodes when they air together with the face of the interviewee) -> this will link to the respective episodes
- please design an "bright gatherings" book cover mockup to be inluded as a banner -> this will link to Orindel
- subscribe to the newsletter - a banner capturing the name and email of the user -> to be connected to PostWren.
-> a working episode search.

2) Episodes page
- the show will be divided into seasons (12 episodes each) and each episode will need a separate "blog entry" including:
-> A short article (4-5 paragraphs) + stock image
-> interviewee's bio and social links

3) Meet the hosts page
- including bios of the two hosts of the show
- links to their social profiles
- a "request speaker availability" form which sends an email

Some additional nice-to-haves:
1) Good and clean Bio's would be awesome (both for the hosts & the interviewees),
2) an easily navigable episode system,
3) a keyword/date search option
4) easy to share options (share to WhatsApp, Facebook, Twitter, LinkedIn) 5) We must be able to track how the podcasts are shared (google analytics?)

```html
<!DOCTYPE html>
<html lang="en">
<head>
<meta charset="utf-8">
<title>Bright Gatherings — Podcast</title>
<link href="https://fonts.googleapis.com/css2?family=Open+Sans:wght@300;400;600;700&display=swap" rel="stylesheet">
<style>
:root{
  --accent:#f3320b;
  --ink:#111111;
  --light:#ffffff;
  --nav:#e4e4e4;
  --card:#e9e9e9;
  --dark:#0c0c0c;
  --hero-a:#a3aaaf;
  --hero-b:#3b4246;
}
*{box-sizing:border-box;margin:0;padding:0}
html,body{width:1200px;height:3093px;overflow:hidden}
body{position:relative;font-family:"Open Sans",sans-serif;color:var(--ink);background:var(--light)}
.abs{position:absolute}
.btn{position:absolute;display:flex;align-items:center;justify-content:center;font-weight:700;font-size:16px;text-transform:uppercase;background:var(--accent);color:var(--light)}
.section-title{position:absolute;font-weight:700;font-size:32px;text-transform:uppercase;border-left:2px solid var(--accent);padding-left:12px;line-height:30px}
.section-title span{color:var(--accent)}

/* header */
.topbar{left:0;top:0;width:1200px;height:102px;background:var(--accent)}
.social-sq{width:34px;height:34px;background:var(--ink);top:34px}
.brand{left:530px;top:30px;width:140px;height:42px;display:flex;align-items:center;justify-content:center;gap:8px;color:var(--light);font-weight:700;font-size:16px;line-height:18px;text-align:left}
.brand i{display:block;flex:none;width:14px;height:14px;border-radius:50%;background:var(--ink)}
.call{left:948px;top:28px;color:var(--light);display:flex;gap:10px;align-items:center}
.call .ico{width:30px;height:30px;border-radius:50%;background:var(--light);display:flex;align-items:center;justify-content:center}
.call small{display:block;font-size:15px}
.call b{font-size:17px}

.navbar{left:0;top:102px;width:1200px;height:54px;background:var(--nav)}
.nav-link{top:116px;font-weight:600;font-size:18px}
.nav-link.active::after{content:"";position:absolute;left:0;right:0;bottom:-10px;height:3px;background:var(--accent)}
.search{left:960px;top:115px;width:142px;height:29px;border:1px solid var(--accent);background:var(--light);font-size:15px;padding:4px 6px;color:#333}

/* hero */
.hero{left:0;top:156px;width:1200px;height:546px;background:linear-gradient(120deg,var(--hero-a),#6b7378 55%,var(--hero-b))}
.book{left:174px;top:220px;width:254px;height:412px;background:linear-gradient(160deg,#f3320b,#f9a11a);box-shadow:12px 0 0 #e8e8e8}
.hero-title{left:622px;top:272px;width:400px;text-align:center;color:var(--light);font-size:34px;font-weight:700}
.hero-title span{color:var(--accent)}
.hero-text{left:550px;top:348px;width:540px;text-align:center;color:var(--light);font-size:22px;font-weight:300;line-height:23px}
.dot{top:661px;width:15px;height:15px;border-radius:50%;background:var(--light)}

/* about */
.about-text{left:100px;top:870px;width:582px;font-size:15px;line-height:30px;text-align:justify}
.frame{left:778px;top:804px;width:321px;height:282px;border:5px solid var(--accent);border-radius:4px}
.about-photo{left:754px;top:834px;width:310px;height:270px;background:linear-gradient(135deg,#6b3a2a,#2a2f3a 60%,#8b8f99)}
.play{left:910px;top:938px;width:22px;height:15px;border-radius:4px;background:#e21c1c}

/* hosts */
.hosts{left:0;top:1205px;width:1200px;height:571px;background:radial-gradient(circle at 50% 40%,#2a2420,var(--dark) 70%)}
.host-photo{width:232px;height:232px;border-radius:50%;top:1359px}
.host-name{top:1615px;width:300px;text-align:center;color:var(--light);font-weight:700;font-size:20px}
.host-role{top:1645px;width:300px;text-align:center;color:var(--light);font-size:18px}

/* episodes */
.card{top:1964px;width:307px;height:458px;background:var(--card);border:1px solid #555}
.card-photo{position:absolute;left:0;top:0;width:100%;height:174px}
.card-dot{position:absolute;left:139px;top:162px;width:28px;height:28px;border-radius:50%;background:var(--accent)}
.card-num{position:absolute;top:198px;width:100%;text-align:center;font-size:17px}
.card-title{position:absolute;top:230px;width:100%;text-align:center;font-weight:700;font-size:16px;line-height:26px}
.card-desc{position:absolute;top:302px;left:25px;width:257px;text-align:center;font-size:15px;line-height:28.5px}
.card .btn{left:51px;top:440px;width:205px;height:36px}

/* newsletter */
.newsletter{left:0;top:2542px;width:1200px;height:240px;background:var(--dark)}
.news-title{left:0;top:2568px;width:1200px;text-align:center;color:var(--light);font-weight:700;font-size:32px}
.news-title span{color:var(--accent)}
.news-text{left:350px;top:2630px;width:500px;text-align:center;color:var(--light);font-size:16px;line-height:21px}
.email{left:406px;top:2714px;width:238px;height:39px;background:var(--light);font-size:14px;padding:10px 8px}

/* footer */
.footer{left:0;top:2782px;width:1200px;height:311px;background:var(--accent);color:var(--light)}
.f-head{top:2806px;font-weight:700;font-size:16px;color:var(--light)}
.f-text{left:98px;top:2846px;width:255px;font-size:15px;line-height:23px;text-align:justify;color:var(--light)}
.f-link{left:431px;font-size:16px;color:var(--light)}
.f-contact{left:636px;font-size:16px;line-height:20px;color:var(--light);display:flex;gap:10px}
.f-sq{top:2984px;width:20px;height:20px;background:var(--light);border-radius:3px}
.f-brand{left:900px;top:2850px;width:210px;text-align:center;font-weight:700;font-size:28px;line-height:34px;color:var(--light)}
.f-rule{left:98px;top:3036px;width:1002px;height:1px;background:#f7a08c}
.copy{left:0;top:3050px;width:1200px;text-align:center;font-size:16px;color:var(--light)}
</style>
</head>
<body>

<header>
  <div class="abs topbar"></div>
  <div class="abs social-sq" style="left:98px" role="img" aria-label="Social profile"></div>
  <div class="abs social-sq" style="left:136px" role="img" aria-label="Social profile"></div>
  <div class="abs social-sq" style="left:174px" role="img" aria-label="Social profile"></div>
  <div class="abs social-sq" style="left:212px" role="img" aria-label="Social profile"></div>
  <div class="abs social-sq" style="left:250px" role="img" aria-label="Social profile"></div>
  <div class="abs brand"><i></i><span>Bright<br>Gatherings</span></div>
  <div class="abs call">
    <div class="ico"><svg width="16" height="16" viewBox="0 0 24 24"><path d="M6.6 10.8a15 15 0 0 0 6.6 6.6l2.2-2.2c.3-.3.7-.4 1-.2 1.1.4 2.3.6 3.6.6.6 0 1 .4 1 1V20c0 .6-.4 1-1 1A17 17 0 0 1 3 4c0-.6.4-1 1-1h3.5c.6 0 1 .4 1 1 0 1.3.2 2.5.6 3.6.1.3 0 .7-.2 1z" fill="#f3320b"/></svg></div>
    <div><small>call us</small><b>555-210-0148</b></div>
  </div>

  <div class="abs navbar"></div>
  <nav>
    <span class="abs nav-link" style="left:97px">Home</span>
    <span class="abs nav-link" style="left:190px">About</span>
    <span class="abs nav-link active" style="left:283px">Episode</span>
    <span class="abs nav-link" style="left:391px">Training</span>
    <span class="abs nav-link" style="left:503px">Meet the host</span>
    <span class="abs nav-link" style="left:650px">Contact</span>
  </nav>
  <div class="btn" style="left:785px;top:115px;width:151px;height:29px;font-size:15px">Get Book Now</div>
  <div class="abs search">Search
    <svg style="position:absolute;right:6px;top:6px" width="16" height="16" viewBox="0 0 16 16"><circle cx="6.5" cy="6.5" r="5" fill="none" stroke="#666" stroke-width="1.5"/><path d="M10.5 10.5L15 15" stroke="#666" stroke-width="1.5"/></svg>
  </div>
</header>

<section>
  <div class="abs hero"></div>
  <div class="abs book" role="img" aria-label="Bright Gatherings book cover mockup"></div>
  <h1 class="abs hero-title">BRIGHT <span>GATHERING</span></h1>
  <p class="abs hero-text">Lorem Ipsum is simply dummy text of the printing and typesetting industry. Lorem Ipsum has been the industry's standard dummy text</p>
  <div class="btn" style="left:648px;top:464px;width:203px;height:36px">Get the Book Now</div>
  <div class="btn" style="left:872px;top:464px;width:130px;height:36px;background:#fff;color:var(--ink)">Get Trained</div>
  <div class="abs dot" style="left:569px"></div>
  <div class="abs dot" style="left:591px;background:var(--accent)"></div>
  <div class="abs dot" style="left:613px"></div>
</section>

<section>
  <h2 class="section-title" style="left:98px;top:808px">About <span>Us</span></h2>
  <p class="abs about-text">Lorem Ipsum is simply dummy text of the printing and typesetting industry. Lorem Ipsum has been the industry's standard dummy text ever since the 1500s, when an unknown printer took a galley of type and scrambled it to make a type specimen book. It has survived not only five centuries, but also the leap into electronic typesetting, remaining essentially unchanged. It was popularised in the 1960s with the release of Letraset sheets containing Lorem Ipsum passages,</p>
  <div class="btn" style="left:98px;top:1078px;width:141px;height:31px;font-size:15px">Learn More&nbsp;<svg width="16" height="10" viewBox="0 0 16 10"><path d="M0 5h14M10 1l4 4-4 4" stroke="#fff" stroke-width="1.5" fill="none"/></svg></div>
  <div class="abs frame"></div>
  <div class="abs about-photo" role="img" aria-label="Speaker presenting on stage to a large audience"></div>
  <div class="abs play"></div>
</section>

<section>
  <div class="abs hosts" role="img" aria-label="Audience background"></div>
  <h2 class="section-title" style="left:459px;top:1248px;color:#fff;border-left-color:#fff">Meet the <span>Hosts</span></h2>
  <div class="abs host-photo" style="left:179px;background:linear-gradient(135deg,#c9c2b8,#4a4e58)" role="img" aria-label="Portrait of host Tomas Vell"></div>
  <div class="abs host-photo" style="left:484px;background:linear-gradient(135deg,#4a8bd0,#1f3f6e)" role="img" aria-label="Portrait of host Ravi Calder"></div>
  <div class="abs host-photo" style="left:790px;background:linear-gradient(135deg,#e6e2dc,#9c9a95)" role="img" aria-label="Portrait of trainer Mara Quill"></div>
  <div class="abs host-name" style="left:145px">TOMAS VELL</div>
  <div class="abs host-role" style="left:145px">Lead Author</div>
  <div class="abs host-name" style="left:450px">RAVI CALDER</div>
  <div class="abs host-role" style="left:450px">Co Author</div>
  <div class="abs host-name" style="left:756px">MARA QUILL</div>
  <div class="abs host-role" style="left:756px">Trainer</div>
  <div class="btn" style="left:532px;top:1712px;width:133px;height:28px;font-size:15px">View All</div>
</section>

<section>
  <h2 class="section-title" style="left:382px;top:1876px">Latest Podcast <span>Episodes</span></h2>

  <article class="abs card" style="left:98px">
    <div class="card-photo" style="background:linear-gradient(135deg,#9b5a45,#d8d2cc)" role="img" aria-label="Guest smiling in an office"></div>
    <div class="card-dot"></div>
    <div class="card-num">Episode 195:</div>
    <div class="card-title">Stop Apologizing for Your<br>ONE Thing | Dana Morrow</div>
    <div class="card-desc">Do you ever feel guilty because you're not perfectly prioritizing Your ONE Thing, or because you're not as successful as you'd like to be?</div>
    <div class="btn">Explore</div>
  </article>

  <article class="abs card" style="left:445px">
    <div class="card-photo" style="background:linear-gradient(135deg,#d7d3ce,#b9b2aa)" role="img" aria-label="Guest pointing with a smile"></div>
    <div class="card-dot"></div>
    <div class="card-num">Episode 194:</div>
    <div class="card-title">Stop Apologizing for Your<br>ONE Thing | Dana Morrow</div>
    <div class="card-desc">Do you ever feel guilty because you're not perfectly prioritizing Your ONE Thing, or because you're not as successful as you'd like to be?</div>
    <div class="btn">Explore</div>
  </article>

  <article class="abs card" style="left:792px">
    <div class="card-photo" style="background:linear-gradient(135deg,#cfd3d6,#7d838a)" role="img" aria-label="Two colleagues looking at a tablet"></div>
    <div class="card-dot"></div>
    <div class="card-num">Episode 193:</div>
    <div class="card-title">Stop Apologizing for Your<br>ONE Thing | Dana Morrow</div>
    <div class="card-desc">Do you ever feel guilty because you're not perfectly prioritizing Your ONE Thing, or because you're not as successful as you'd like to be?</div>
    <div class="btn">Explore</div>
  </article>
</section>

<section>
  <div class="abs newsletter"></div>
  <h2 class="abs news-title">NEWS<span>LETTER</span></h2>
  <p class="abs news-text">Lorem Ipsum is simply dummy text of the printing and typesetting industry. Lorem Ipsum has been the industry's standard dummy text ever since the 1500s</p>
  <div class="abs email">Enter Your Email</div>
  <div class="btn" style="left:644px;top:2714px;width:148px;height:39px">Subscribe</div>
</section>

<footer>
  <div class="abs footer"></div>
  <h3 class="abs f-head" style="left:98px">ABOUT</h3>
  <p class="abs f-text">Lorem Ipsum is simply dummy text of the printing and typesetting industry. Lorem Ipsum has been the industry's standard dummy text ever since the 1500s</p>
  <div class="abs f-sq" style="left:98px" role="img" aria-label="Social profile"></div>
  <div class="abs f-sq" style="left:126px" role="img" aria-label="Social profile"></div>
  <div class="abs f-sq" style="left:160px" role="img" aria-label="Social profile"></div>
  <div class="abs f-sq" style="left:195px" role="img" aria-label="Social profile"></div>

  <h3 class="abs f-head" style="left:428px">QUICK LINKS</h3>
  <span class="abs f-link" style="top:2838px">Home</span>
  <span class="abs f-link" style="top:2868px">About</span>
  <span class="abs f-link" style="top:2898px">Episodes</span>
  <span class="abs f-link" style="top:2928px">Training</span>
  <span class="abs f-link" style="top:2958px">Meet the host</span>
  <span class="abs f-link" style="top:2988px">Shop</span>

  <h3 class="abs f-head" style="left:636px">Contact Us</h3>
  <div class="abs f-contact" style="top:2840px"><svg width="14" height="18" viewBox="0 0 14 18"><path d="M7 0a7 7 0 0 0-7 7c0 5 7 11 7 11s7-6 7-11a7 7 0 0 0-7-7zm0 10a3 3 0 1 1 0-6 3 3 0 0 1 0 6z" fill="#fff"/></svg><span>Linden Quay West,<br>Harbourside 4021</span></div>
  <div class="abs f-contact" style="top:2894px"><svg width="16" height="16" viewBox="0 0 24 24"><path d="M6.6 10.8a15 15 0 0 0 6.6 6.6l2.2-2.2c.3-.3.7-.4 1-.2 1.1.4 2.3.6 3.6.6.6 0 1 .4 1 1V20c0 .6-.4 1-1 1A17 17 0 0 1 3 4c0-.6.4-1 1-1h3.5c.6 0 1 .4 1 1 0 1.3.2 2.5.6 3.6.1.3 0 .7-.2 1z" fill="none" stroke="#fff" stroke-width="1.6"/></svg><span>+1 555-013-0695</span></div>
  <div class="abs f-contact" style="top:2927px"><svg width="16" height="16" viewBox="0 0 16 16"><rect x="1" y="3" width="14" height="10" fill="none" stroke="#fff"/><path d="M1 3l7 6 7-6" fill="none" stroke="#fff"/></svg><span>hello@brightgatherings.example</span></div>

  <div class="abs f-brand">Bright<br>Gatherings</div>
  <div class="abs f-rule"></div>
  <p class="abs copy">Copyrights @2019 All Rights Resrverd</p>
</footer>

</body>
</html>
```